Business Card Design - Property Management & Real Estate Services

I need a business card design for my company that I can print ZEPLA Cards. The company is called Brindle Management Company. It is a property management and real estate company. The design has to be clean and modern. I need two versions. One for my employee and one for me. However, the design will be the same, just different text. You can get a feel for the company by looking at our website at www.brindlemanagement.example.

Industry/Entity Type

Property Management

Contact Information for Business Card

I will be using ZEPLA.com to print my cards. I will most likely use the rounded edges card. I need two versions, however, they will be the same design. I need one for me and my employee.

Colors
3276b5
33a6d7

Requirements
Must have
• Company Logo
• Name of person
• Property Management & Real Estate Service
• Phone
• Email
• Website
• Address
• A space to place a QR code

```html
<!DOCTYPE html>
<html lang="en">
<head>
<meta charset="utf-8">
<title>Brindle Management – Business Cards</title>
<link href="https://fonts.googleapis.com/css2?family=Roboto:wght@400;500;700&family=Roboto+Condensed:wght@700&display=swap" rel="stylesheet">
<style>
  :root {
    --page-bg: #c9c9c9;
    --card-bg: #ffffff;
    --blue-deep: #1f55a8;
    --blue-brand: #3276b5;
    --blue-soft: #5b93d3;
    --blue-pale: #dbe8f6;
    --text-dark: #333333;
  }
  * { box-sizing: border-box; margin: 0; padding: 0; }
  html, body { width: 1200px; height: 852px; overflow: hidden; }
  body {
    background: var(--page-bg);
    font-family: "Roboto", Arial, sans-serif;
    position: relative;
  }
  .card {
    position: absolute;
    width: 540px;
    height: 310px;
    background: var(--card-bg);
    border-radius: 18px;
    overflow: hidden;
    box-shadow: 0 4px 14px rgba(0,0,0,0.18);
  }
  /* Front */
  .card--front { left: 50px; top: 150px; }
  .front-brand {
    position: absolute;
    top: 98px; left: 0; right: 0;
    text-align: center;
  }
  .brand-name {
    font-family: "Roboto", Arial, sans-serif;
    font-weight: 500;
    color: var(--blue-deep);
    letter-spacing: 1px;
  }
  .front-brand .brand-name { font-size: 40px; line-height: 1.1; }
  .front-web {
    position: absolute;
    top: 218px; left: 0; right: 0;
    display: flex; align-items: center; justify-content: center; gap: 12px;
    font-size: 14px; color: var(--text-dark);
  }
  .front-web .rule { width: 40px; height: 2px; background: var(--blue-brand); }
  .front-band {
    position: absolute; left: 0; right: 0; bottom: 0; height: 12px;
    display: flex;
  }
  .front-band .band-soft { flex: 1; background: var(--blue-soft); }
  .front-band .band-deep { flex: 1.1; background: var(--blue-deep); }

  /* Back */
  .card--back { left: 610px; top: 390px; }
  .back-brand {
    position: absolute; top: 36px; left: 34px;
  }
  .back-brand .brand-name { font-size: 28px; }
  .person { position: absolute; top: 112px; left: 34px; }
  .person-name {
    font-family: "Roboto Condensed", "Roboto", sans-serif;
    font-weight: 700; font-size: 20px; color: var(--blue-deep);
  }
  .person-role { font-size: 14px; color: var(--text-dark); margin-top: 4px; }
  .contact { position: absolute; top: 184px; left: 34px; list-style: none; }
  .contact li {
    display: flex; align-items: center; gap: 10px;
    font-size: 13.5px; color: var(--text-dark); line-height: 21px;
  }
  .contact svg { width: 13px; height: 13px; flex: none; fill: var(--blue-deep); }
  .contact .plain { padding-left: 23px; }
  .back-graphic {
    position: absolute; right: 0; top: 0; bottom: 0; width: 200px;
    background: linear-gradient(160deg, var(--blue-pale), #ffffff 75%);
  }
</style>
</head>
<body>

<section class="card card--front" aria-label="Card front">
  <div class="front-brand"><span class="brand-name">Brindle Management</span></div>
  <div class="front-web"><span class="rule"></span><span>www.brindlemanagement.example</span><span class="rule"></span></div>
  <div class="front-band"><span class="band-soft"></span><span class="band-deep"></span></div>
</section>

<section class="card card--back" aria-label="Card back">
  <div class="back-brand"><span class="brand-name">Brindle Management</span></div>
  <div class="person">
    <div class="person-name">Mateo R. Salcedo</div>
    <div class="person-role">Founder</div>
  </div>
  <ul class="contact">
    <li><svg viewBox="0 0 24 24"><path d="M6.6 10.8a15 15 0 0 0 6.6 6.6l2.2-2.2c.3-.3.7-.4 1-.2 1.1.4 2.3.6 3.6.6.6 0 1 .4 1 1V20c0 .6-.4 1-1 1A17 17 0 0 1 3 4c0-.6.4-1 1-1h3.5c.6 0 1 .4 1 1 0 1.3.2 2.5.6 3.6.1.3 0 .7-.2 1z"/></svg>(555) 014-2286</li>
    <li><svg viewBox="0 0 24 24"><path d="M2 5h20v14H2zM4 7v.5l8 5 8-5V7l-8 5z"/></svg>mateo@brindlemanagement.example</li>
    <li><svg viewBox="0 0 24 24"><circle cx="12" cy="12" r="10"/></svg>www.brindlemanagement.example</li>
    <li class="plain">480 Harbor Ave #300 Coral Bay, FL 33000</li>
  </ul>
  <div class="back-graphic" role="img" aria-label="Large outlined building skyline decoration in brand blue"></div>
</section>

</body>
</html>
```